Summer Sunglass offer

Need a poster design for a spring / summer campaign. We are an opticians with good footfall. The design needs to be eye catching and aimed at 40 year old plus. The offer is Up to 50% off sunglass offer, t&c apply. (I have attached our last year campaign)
Also need a 2 sided A5 leaflet design (see attached)
I've uploaded a copy of our logo

A5 leaflet should read:

Grab a bargain on two great looks this summer Upto 50% off sunglasses
Look great and stay safe in the sun this summer

We want you to look great, feel fantastic and most of all stay safe in the sun this summer. That’s why we’re offering you 50% off prescription sunglasses with every complete pair of glasses you buy this summer or 25% off for prescription sunglasses with no other purchase.
Find you new summer looks from our gorgeous collection of frames in store. It matters to us that you look great in your new glasses as much as how well you see through them, so we’ll be on hand to help you find frames that suit you best.
What new looks will you go for? Smart or sassy? Formal or Fun? Whatever you’re in the mood for, you’ll find it in our collections this summer.
Call in today to find your new looks, and remember to bring your prescription if you don’t need an eye test.

Target Market(s)

40 + year old

Industry/Entity Type

Optician

Colors

Designer to choose colors to be used in the design.

Requirements
Must have
• Images, preferably a male and Female image

```html
<!DOCTYPE html>
<html lang="en">
<head>
<meta charset="utf-8">
<title>Summer Sunglasses Offer – Brookfield Eyecare Centre</title>
<link rel="stylesheet" href="https://fonts.googleapis.com/css2?family=Lato:wght@400;700&display=swap">
<style>
  :root {
    --teal: #58a9b4;
    --offer-red: #e30a3d;
    --white: #ffffff;
    --ink-teal: #4a9fab;
  }
  * { margin: 0; padding: 0; box-sizing: border-box; }
  html, body {
    width: 851px;
    height: 1200px;
    overflow: hidden;
    background: var(--white);
  }
  .leaflet {
    position: relative;
    width: 851px;
    height: 1200px;
    font-family: "Lato", sans-serif;
    color: var(--white);
    text-align: center;
  }
  .headline-band {
    height: 142px;
    background: var(--teal);
    padding-top: 11px;
    font-size: 29px;
    line-height: 35.5px;
    white-space: nowrap;
  }
  .headline-band strong { font-weight: 700; }
  .offer-panel {
    height: 897px;
    background: var(--offer-red);
    padding-top: 21px;
    font-size: 31.5px;
    line-height: 41px;
    white-space: nowrap;
  }
  .offer-panel p { margin-bottom: 35px; }
  .offer-panel p:last-child { margin-bottom: 0; }
  .offer-panel strong { font-weight: 700; }
  .divider-stripe {
    height: 13px;
    background: var(--teal);
  }
  .brand-footer {
    position: relative;
    height: 148px;
  }
  .brand-lockup {
    position: absolute;
    top: 29px;
    left: 0;
    width: 100%;
    display: flex;
    justify-content: center;
    align-items: center;
    gap: 14px;
  }
  .brand-mark { width: 36px; height: 36px; }
  .brand-name {
    font-size: 24px;
    font-weight: 700;
    color: var(--ink-teal);
    letter-spacing: 1.5px;
  }
  .web-address {
    position: absolute;
    top: 108px;
    left: 0;
    width: 100%;
    font-size: 23.5px;
    color: var(--ink-teal);
  }
</style>
</head>
<body>
<main class="leaflet">
  <header class="headline-band">
    <div>GRAB A BARGAIN ON TWO GREAT LOOKS THIS SUMMER</div>
    <div><strong>UPTO 50% OFF SUNGLASSES.</strong></div>
    <div>LOOK GREAT AND STAY SAFE IN THE SUN THIS SUMMER.</div>
  </header>

  <section class="offer-panel">
    <p>We want you to look great, feel fantastic and<br>
    most of all stay safe in the sun this summer.<br>
    That’s why we’re offering you <strong>50</strong>% off prescription<br>
    sunglasses with every complete pair of glasses<br>
    you buy this summer<br>
    or <strong>25</strong>% off for prescription sunglasses<br>
    with no other purchase.</p>

    <p>Find you new summer looks from our gorgeous<br>
    collection of frames in store.<br>
    It matters to us that you love how you look<br>
    in your new glasses as much as how well<br>
    you see through them,<br>
    so we’ll be on hand to help you find frames<br>
    that suit you best.<br>
    What new looks will you go for? Smart or sassy?<br>
    Formal or Fun? Whatever you’re in the mood for,<br>
    you’ll find it in our collections this summer.</p>

    <p>Call in today to find your new looks, and remember<br>
    to bring your prescription if you don’t need an eye test.</p>
  </section>

  <div class="divider-stripe"></div>

  <footer class="brand-footer">
    <div class="brand-lockup">
      <svg class="brand-mark" viewBox="0 0 36 36" aria-hidden="true">
        <circle cx="18" cy="18" r="14.5" fill="none" stroke="var(--teal)" stroke-width="5"/>
      </svg>
      <span class="brand-name">BROOKFIELD EYECARE CENTRE</span>
    </div>
    <div class="web-address">brookfieldeyecare.co.uk</div>
  </footer>
</main>
</body>
</html>
```